Corporate Design für logopädische Praxis
Zielgruppe
Ich gründe eine logopädische Praxis, die Sprachtherapie sowohl für Erwachsene als auch Kinder anbietet und damit ein Logo benötigt, das jede Altersgruppe anspricht und 'Lindenhof' als fachliche und menschliche Qualitätszeit interpretiert.
Aufgabenstellung
Ich bevorzuge ein klares Design, welches das Wortspiel der 'Lindenhof' im Idealfall aufgreift und den Patienten vermittelt, dass sowohl die fachliche Qualität der Behandlung als auch die Ebene von Empathie und Patientenorientierung im zwischenmenschlichen Umgang für die Praxis zentral sind.

```html
<!DOCTYPE html>
<html lang="de">
<head>
<meta charset="utf-8">
<title>Lindenhof – Praxis für Logopädie · Geschäftsausstattung</title>
<link rel="stylesheet" href="https://fonts.googleapis.com/css2?family=Mukta:wght@300;400&display=swap">
<style>
:root{
  --mauve:#9c90a8;
  --sand:#c9a080;
  --ink:#1e1e1e;
  --paper:#ffffff;
  --edge:#b9b9b9;
  --shadow:rgba(0,0,0,.28);
  --mist:#f1f0f3;
  --sign:#e6eaf4;
}
*{box-sizing:border-box;margin:0;padding:0}
html,body{width:1200px;height:856px;overflow:hidden;background:var(--paper)}
body{position:relative;font-family:"Mukta",sans-serif;font-weight:300;color:var(--ink)}

.brand{position:absolute;display:flex;align-items:flex-start;gap:.3em}
.brand__dot{flex:none;border-radius:50%;background:var(--mauve)}
.brand__text{display:flex;flex-direction:column}
.brand__name{color:var(--mauve);font-weight:300;line-height:1;letter-spacing:.005em}
.brand__tag{color:var(--sand);font-weight:300;line-height:1.1;margin-left:1.2em}

.brand--hero{left:138px;top:180px}
.brand--hero .brand__dot{width:30px;height:30px;margin-top:18px}
.brand--hero .brand__name{font-size:62px}
.brand--hero .brand__tag{font-size:19px;margin-left:42px;margin-top:2px}

.sheet{position:absolute;background:var(--paper);border:1px solid var(--edge);box-shadow:8px 10px 6px var(--shadow)}

.envelope{left:59px;top:443px;width:521px;height:260px}
.envelope__window{position:absolute;left:54px;top:125px;width:173px;height:95px;border:1px solid var(--edge);border-radius:8px}
.brand--small .brand__dot{width:13px;height:13px;margin-top:6px}
.brand--small .brand__name{font-size:25px}
.brand--small .brand__tag{font-size:9.5px;margin-left:20px}
.envelope .brand{left:54px;top:30px}

.card{width:241px;height:155px}
.card--front{left:315px;top:414px}
.card--front .brand{left:53px;top:32px}
.card__name{position:absolute;left:0;right:0;top:98px;text-align:center;color:var(--mauve);font-size:11.5px}
.contact{position:absolute;display:flex;gap:6px;font-size:8.2px;line-height:1.3;color:var(--sand)}
.contact::before{content:"";flex:none;width:5px;height:5px;margin-top:3px;border-radius:50%;background:var(--mauve)}
.card--back{left:314px;top:579px;overflow:hidden}
.card__web{position:absolute;left:0;right:0;top:111px;text-align:center;font-size:8.4px;line-height:1.3;color:var(--sand)}
.deco{position:absolute;border-radius:50%;background:var(--mist)}
.card--back .deco{left:120px;top:36px;width:38px;height:38px}

.letter{left:605px;top:46px;width:542px;height:766px;overflow:hidden}
.letter .brand{left:207px;top:40px}
.brand--mid .brand__dot{width:16px;height:16px;margin-top:8px}
.brand--mid .brand__name{font-size:31px}
.brand--mid .brand__tag{font-size:11px;margin-left:24px}
.letter .deco{left:342px;top:514px;width:58px;height:58px}
.letter__sender{position:absolute;left:64px;top:122px;font-size:6px;color:var(--sand)}
.letter__recipient,.letter__body,.letter__close{position:absolute;left:64px;font-size:8.3px;line-height:12.8px;font-weight:400}
.letter__recipient{top:150px}
.letter__body{top:293px;width:352px}
.letter__body p{margin-bottom:12.8px}
.letter__close{top:561px}
.letter__signature{position:absolute;left:56px;top:586px;width:100px;height:26px;background:var(--sign)}
.letter__signer{position:absolute;left:64px;top:612px;font-size:8.3px;font-weight:400}
.fold{position:absolute;left:10px;width:3px;height:1px;background:var(--sand)}
.letter__foot{position:absolute;top:712px;left:0;width:100%}
.letter__foot .contact{font-size:8.3px}
</style>
</head>
<body>

<div class="brand brand--hero">
  <span class="brand__dot"></span>
  <div class="brand__text"><span class="brand__name">Lindenhof</span><span class="brand__tag">Praxis für Logopädie</span></div>
</div>

<div class="sheet envelope">
  <div class="brand brand--small">
    <span class="brand__dot"></span>
    <div class="brand__text"><span class="brand__name">Lindenhof</span><span class="brand__tag">Praxis für Logopädie</span></div>
  </div>
  <div class="envelope__window"></div>
</div>

<div class="sheet card card--front">
  <div class="brand brand--small">
    <span class="brand__dot"></span>
    <div class="brand__text"><span class="brand__name">Lindenhof</span><span class="brand__tag">Praxis für Logopädie</span></div>
  </div>
  <div class="card__name">Carla Wendt</div>
  <div class="contact" style="left:34px;top:120px">Lindenweg 14<br>28195 Birkenfeld</div>
  <div class="contact" style="left:135px;top:120px">T: 0421/5583210<br>M: 0171/4402918</div>
</div>

<div class="sheet card card--back">
  <span class="deco"></span>
  <div class="card__web">info@lindenhof-praxis.de<br>www.lindenhof-praxis.de</div>
</div>

<div class="sheet letter">
  <span class="deco"></span>
  <div class="brand brand--mid">
    <span class="brand__dot"></span>
    <div class="brand__text"><span class="brand__name">Lindenhof</span><span class="brand__tag">Praxis für Logopädie</span></div>
  </div>
  <div class="letter__sender">Lindenhof · Lindenweg 14 · 28195 Birkenfeld</div>
  <div class="letter__recipient">Jonas Brehm<br>Ahornallee 7<br><br>28195 Birkenfeld</div>
  <span class="fold" style="top:268px"></span>
  <span class="fold" style="top:373px"></span>
  <div class="letter__body">
    <p style="margin-bottom:11px">Sehr geehrter Herr Brehm,</p>
    <p>im il illaore feuis et vel dolenibh euis nibh ent praestis ad eum acil delit aliquipit vullan ute commod do dipsusto dolutat, verit lortinissim endio od tem veros am zzriliquamet wiscin veros et nonsed dolor irit iliscil euismod et, sum eril irit amet, consequi et euissim irit eugue vulputpat alit ad euipisi esequam, consequat utem nos etum vullan ut amconsequi bla feugue min eugait, quatinibh etumsan henim adit enit vulla accum ing ex enim iliquis nim voloreet luptat. Olesendre tin ercilit aut dolum zzrit nostrud dolorer augiam, quam duis dolore do dipit augait wis adiatet vel et, con ercilit lum zzrit lam ea core commodolor<br>Isi erit at, quatisi. Duisl in eugue te te min heniat. Ut velit lorem quiscid uissectem eliquismolor acincilla feuipis eugue feu feum et, quis dolorpe rillam dolobortin volor am, quam velit sed minisci llutat. Ipisl ex eum in henibh elendre facilit velit, corem nonsequis accum velismo lutat.</p>
    <p>Loreet vendre magna conum quat wisl irit ute tio corperc ilismodo etuer sum velendrer suscin ea core magna facincipis ad te feu facidui ssectem quipsum ip eraessed tetuer sisim velit velit ex et, quatem duissenisi bla feugait ad magna consequam, vulputatem dolore feu feuis er irilit augait prate feu faciduis nit dipis ationse dolore delis ad te tat.</p>
    <p>Ibh etumsandre veratum zzrit, quip</p>
  </div>
  <div class="letter__close">Mit freundlichen Grüßen</div>
  <div class="letter__signature" role="img" aria-label="Handschriftliche Unterschrift"></div>
  <div class="letter__signer">Carla Wendt</div>
  <div class="letter__foot">
    <div class="contact" style="left:210px">Lindenweg 14<br>28195 Birkenfeld</div>
    <div class="contact" style="left:337px">T: 0421/5583210<br>M: 0171/4402918</div>
    <div class="contact" style="left:418px">info@lindenhof-praxis.de<br>www.lindenhof-praxis.de</div>
  </div>
</div>

</body>
</html>
```